Corvel Creamery Works ( Australian Dairy site )

We need a new website we are a new company in Australia manufacturing dairy products ( Packing Butter ) We want to have a new modern punchy website with the basic details of the company and company certifications should be linked in a pdf etc.. maybe photos of the site modernised graphics etc.. we need to show our customers our brand clean and green image of Australian high quality products packed under strict Australian quality standards.

Target Market(s)

export - Asia

Industry/Entity Type

It Company

Number of Pages Required

5+ page

Requirements
Must have
• Home page
• About us page
• Products page
• Contact us page
• Facility / Accreditations ( Under facility pdf files eg Licenses, halal etc.. )

```html
<!DOCTYPE html>
<html lang="en">
<head>
<meta charset="utf-8">
<title>Our Products – Corvel Creamery Works</title>
<link href="https://fonts.googleapis.com/css2?family=Damion&family=Josefin+Sans:wght@400;600;700&display=swap" rel="stylesheet">
<style>
:root{
  --sky-top:#cfe6fb;
  --sky-bottom:#5aa9ef;
  --green:#36a03a;
  --green-dark:#2a8a31;
  --green-light:#b6f0a2;
  --orange:#f6a919;
  --white:#ffffff;
  --brown:#5b4c40;
  --brown-light:#6b5b4e;
  --text-grey:#555555;
  --footer-text:#e6ddd3;
  --input-bg:#3f352d;
}
*{margin:0;padding:0;box-sizing:border-box}
html,body{width:764px;height:1200px;overflow:hidden;background:var(--white)}
body{position:relative;font-family:"Josefin Sans",sans-serif}
.backdrop{position:absolute;left:0;top:0;width:764px;height:1200px}
.abs{position:absolute}

.brand{left:86px;top:24px;display:flex;align-items:center;gap:8px}
.brand-dot{width:22px;height:22px;border-radius:50%;background:var(--green)}
.brand-name{font-size:15px;font-weight:600;color:var(--green-dark);line-height:1.05;width:130px}

.main-nav{left:320px;top:43px;display:flex;gap:0}
.main-nav a{font-size:7px;font-weight:600;color:var(--white);text-decoration:none;letter-spacing:.3px;margin-right:26px}
.main-nav a.current{color:var(--green-dark)}
.main-nav a:last-child{margin-right:0}

.script{font-family:"Damion",cursive;font-weight:400;text-align:center;width:764px;left:0}
.page-title{top:118px;font-size:46px;color:var(--white);text-shadow:0 2px 3px rgba(0,0,0,.25)}
.section-title{font-size:32px}
.salted-title{top:258px;color:var(--white)}
.unsalted-title{top:636px;color:var(--green-dark)}

.product{width:166px;text-align:center}
.product-photo{width:166px;height:153px;background:radial-gradient(circle at 50% 50%,#ffffff 0%,#f2f2f2 45%,#d6d6d6 100%);box-shadow:0 1px 3px rgba(0,0,0,.2)}
.product-name{margin-top:14px;font-size:13px;font-weight:600}
.product-tag{margin-top:7px;font-size:9.5px;line-height:13px}
.product-size{margin-top:6px;font-size:7.5px;font-weight:700}
.on-green .product-name{color:var(--white)}
.on-green .product-tag{color:var(--green-light)}
.on-green .product-size{color:var(--white)}
.on-white .product-name{color:var(--green-dark)}
.on-white .product-tag{color:var(--text-grey)}
.on-white .product-size{color:var(--green-dark)}

.footer-heading{font-size:15px;font-weight:600;color:var(--white)}
.quick-links{left:82px;top:1027px}
.quick-links ul{list-style:none;margin-top:10px}
.quick-links li{font-size:7.5px;color:var(--footer-text);line-height:12.2px}
.contact{left:210px;top:1027px}
.contact-line{display:flex;gap:5px;font-size:7.5px;color:var(--footer-text);line-height:12px;margin-top:2px}
.contact-line svg{flex:none;margin-top:2px}
.contact-first{margin-top:12px}
.contact-gap{margin-top:10px}
.newsletter{left:361px;top:1027px}
.newsletter-note{font-size:6.5px;color:var(--footer-text);margin-top:13px}
.email-field{margin-top:11px;width:124px;height:22px;background:var(--input-bg);border:1px solid #4a4037;font-size:6.5px;color:var(--footer-text);padding:8px 6px 0}
.subscribe{margin-top:10px;width:53px;height:17px;background:var(--green);color:var(--white);font-size:6.5px;display:flex;align-items:center;justify-content:center;letter-spacing:.3px}
.footer-brand{left:510px;top:1040px;display:flex;align-items:center;gap:8px}
.footer-brand .brand-dot{width:26px;height:26px;background:#8a7c70}
.footer-brand .brand-name{color:#a99c90;font-size:14px;width:120px}
.social{left:594px;top:1090px;display:flex;gap:3px}
.social span{width:27px;height:27px;border-radius:50%;background:var(--green);display:block}
.copyright{left:0;width:764px;top:1165px;text-align:center;font-size:7px;color:var(--footer-text)}
</style>
</head>
<body>
<svg class="backdrop" viewBox="0 0 764 1200" aria-hidden="true">
  <defs>
    <linearGradient id="sky" x1="0" y1="0" x2="0" y2="1">
      <stop offset="0" stop-color="var(--sky-top)"/>
      <stop offset="1" stop-color="var(--sky-bottom)"/>
    </linearGradient>
    <radialGradient id="meadow" cx="0.5" cy="0.45" r="0.6">
      <stop offset="0" stop-color="#3aa83e"/>
      <stop offset="1" stop-color="#2f9a34"/>
    </radialGradient>
    <linearGradient id="soil" x1="0" y1="0" x2="0" y2="1">
      <stop offset="0" stop-color="var(--brown-light)"/>
      <stop offset="1" stop-color="var(--brown)"/>
    </linearGradient>
  </defs>
  <rect x="0" y="0" width="764" height="260" fill="url(#sky)"/>
  <path d="M0,194 Q382,238 764,194 V300 H0 Z" fill="var(--white)"/>
  <path d="M0,196 Q382,246 764,196 V300 H0 Z" fill="var(--orange)"/>
  <path d="M0,202 Q382,270 764,202 V564 Q382,628 0,564 Z" fill="url(#meadow)"/>
  <rect x="0" y="940" width="764" height="260" fill="url(#soil)"/>
  <path d="M0,940 Q382,1050 764,940 Z" fill="var(--orange)"/>
  <path d="M0,939 Q382,1030 764,939 Z" fill="var(--white)"/>
</svg>

<header>
  <div class="abs brand"><span class="brand-dot"></span><span class="brand-name">Corvel Creamery Works</span></div>
  <nav class="abs main-nav">
    <a href="#">HOME</a><a href="#">ABOUT US</a><a href="#" class="current">PRODUCTS</a><a href="#">FACILITY</a><a href="#">ACCREDITATIONS</a><a href="#">CONTACT US</a>
  </nav>
  <h1 class="abs script page-title">Our Products</h1>
</header>

<main>
  <h2 class="abs script section-title salted-title">Salted Butter</h2>
  <div class="abs product on-green" style="left:84px;top:328px">
    <div class="product-photo" role="img" aria-label="Stacked blocks of salted butter in paper wrappers"></div>
    <div class="product-name">Lorem ipsum dolor</div>
    <div class="product-tag">Pure Australian Butter<br>From our family to yours</div>
    <div class="product-size">7g-10g 227g, 454g, 1KG</div>
  </div>
  <div class="abs product on-green" style="left:299px;top:328px">
    <div class="product-photo" role="img" aria-label="Block of butter on unfolded foil wrapper"></div>
    <div class="product-name">Lorem ipsum dolor</div>
    <div class="product-tag">Pure Australian Butter<br>From our family to yours</div>
    <div class="product-size">7g-10g 227g, 454g, 1KG</div>
  </div>
  <div class="abs product on-green" style="left:514px;top:328px">
    <div class="product-photo" role="img" aria-label="Single-serve butter portion with peeled foil lid"></div>
    <div class="product-name">Lorem ipsum dolor</div>
    <div class="product-tag">Pure Australian Butter<br>From our family to yours</div>
    <div class="product-size">7g-10g 227g, 454g, 1KG</div>
  </div>

  <h2 class="abs script section-title unsalted-title">Unsalted Cultured Butter</h2>
  <div class="abs product on-white" style="left:84px;top:699px">
    <div class="product-photo" role="img" aria-label="Blue and white carton of cultured butter"></div>
    <div class="product-name">Lorem ipsum dolor</div>
    <div class="product-tag">Pure Australian Butter<br>From our family to yours</div>
    <div class="product-size">7g-10g 227g, 454g, 1KG</div>
  </div>
  <div class="abs product on-white" style="left:299px;top:699px">
    <div class="product-photo" role="img" aria-label="Wrapped sticks of butter with red labels"></div>
    <div class="product-name">Lorem ipsum dolor</div>
    <div class="product-tag">Pure Australian Butter<br>From our family to yours</div>
    <div class="product-size">7g-10g 227g, 454g, 1KG</div>
  </div>
  <div class="abs product on-white" style="left:514px;top:699px">
    <div class="product-photo" role="img" aria-label="Two butter blocks in gold foil wrapping"></div>
    <div class="product-name">Lorem ipsum dolor</div>
    <div class="product-tag">Pure Australian Butter<br>From our family to yours</div>
    <div class="product-size">7g-10g 227g, 454g, 1KG</div>
  </div>
</main>

<footer>
  <div class="abs quick-links">
    <h3 class="footer-heading">Quick Links</h3>
    <ul><li>Home</li><li>About us</li><li>Products</li><li>Facility</li><li>Accreditations</li><li>Contact us</li></ul>
  </div>
  <div class="abs contact">
    <h3 class="footer-heading">Contact Us</h3>
    <div class="contact-line contact-first">
      <svg width="7" height="7" viewBox="0 0 10 10"><path d="M2,0.5 L4,3 L3,4.2 Q4.5,6.5 5.8,7 L7,6 L9.5,8 L8.2,9.5 Q3,9 0.5,1.8 Z" fill="var(--footer-text)"/></svg>
      <span>+61 3 5550 1842</span>
    </div>
    <div class="contact-line">
      <svg width="7" height="7" viewBox="0 0 10 10"><rect x="0.7" y="1.8" width="8.6" height="6.4" fill="none" stroke="var(--footer-text)" stroke-width="1"/><path d="M0.7,1.8 L5,5.5 L9.3,1.8" fill="none" stroke="var(--footer-text)" stroke-width="1"/></svg>
      <span>hello@corvelcreamery.example</span>
    </div>
    <div class="contact-line contact-gap">
      <svg width="7" height="8" viewBox="0 0 10 12"><path d="M5,11.5 Q1,6.5 1,4.5 A4,4 0 0 1 9,4.5 Q9,6.5 5,11.5 Z" fill="var(--footer-text)"/><circle cx="5" cy="4.5" r="1.5" fill="var(--brown)"/></svg>
      <span>18 Marlow Lane, Brindale,<br>Victoria 3999 Australia</span>
    </div>
  </div>
  <div class="abs newsletter">
    <h3 class="footer-heading">Newsletter</h3>
    <p class="newsletter-note">Sign Up for Our Newsletter &amp; Promotion</p>
    <div class="email-field">Enter Your email Id</div>
    <div class="subscribe">SUBSCRIBE</div>
  </div>
  <div class="abs footer-brand"><span class="brand-dot"></span><span class="brand-name">Corvel Creamery Works</span></div>
  <div class="abs social" aria-label="Social links"><span></span><span></span><span></span></div>
  <p class="abs copyright">© 2016 corvelcreamery.example</p>
</footer>
</body>
</html>
```